Retail Jewelry Business Card Design Project

We are in need of a new business card design for a retail jewelry store. This store is in the business of fine jewelry including but not specific to bridal jewelry, diamonds, designer jewelry and watches.

This store has been in business for 20 years but continues to strive for a modern professional appeal. The main colors use for this business are a royal blue, white and silver.

Target Market(s)

Target market is ages 18-50

Industry/Entity Type

Jewelry

Requirements
Must have
• Sales Person Name
Sales Person Email Address

Store Address
Store Phone
Website

Standard business card size. No odd shapes or sizes.
Nice to have
• Overall modern feel for card.

We have thought that a design with a nice feature of the logo on the back of the card would be nice but open to ideas.
Should not have
• No specific images of jewelry should be used.

```html
<!DOCTYPE html>
<html lang="en">
<head>
<meta charset="utf-8">
<title>Ellery Vance Fine Jewelry – Business Cards</title>
<link rel="stylesheet" href="https://fonts.googleapis.com/css2?family=Playfair+Display:ital,wght@1,700&family=Source+Sans+3:wght@400;600&display=swap">
<style>
  :root {
    --royal: #2e3592;
    --lilac: #7b74b8;
    --white: #ffffff;
    --stage: #e9e9ee;
    --radius: 22px;
  }
  html, body {
    margin: 0;
    padding: 0;
    width: 1200px;
    height: 751px;
    overflow: hidden;
    background: var(--stage);
    font-family: "Source Sans 3", "Myriad Pro", Arial, sans-serif;
  }
  .canvas {
    position: relative;
    width: 1200px;
    height: 751px;
  }
  .card {
    position: absolute;
    top: 225px;
    width: 525px;
    height: 300px;
    border-radius: var(--radius);
    overflow: hidden;
    box-shadow: 0 6px 18px rgba(0,0,0,0.18);
  }
  .card--front { left: 50px; background: var(--white); }
  .card--back  { left: 625px; background: var(--royal); }

  .card__waves {
    position: absolute;
    inset: 0;
    width: 100%;
    height: 100%;
  }

  .holder-name {
    position: absolute;
    top: 18px;
    left: 0;
    width: 100%;
    text-align: center;
    font-family: "Playfair Display", Georgia, serif;
    font-style: italic;
    font-weight: 700;
    font-size: 17px;
    color: var(--royal);
    letter-spacing: 0.5px;
  }

  .wordmark {
    position: absolute;
    left: 0;
    width: 100%;
    text-align: center;
    font-family: "Source Sans 3", "Myriad Pro", Arial, sans-serif;
    font-weight: 600;
    line-height: 1;
  }
  .wordmark__name { display: block; font-size: 46px; }
  .wordmark__trade { display: block; font-size: 21px; letter-spacing: 5px; margin-top: 8px; }
  .card--front .wordmark { top: 58px; color: var(--royal); }
  .card--back .wordmark  { top: 88px; color: var(--white); }

  .store-address {
    position: absolute;
    left: 110px;
    top: 236px;
    width: 170px;
    text-align: right;
    color: var(--white);
    font-size: 14px;
    line-height: 20px;
  }
  .divider {
    position: absolute;
    left: 292px;
    top: 214px;
    width: 1.5px;
    height: 66px;
    background: var(--white);
  }
  .contact-list {
    position: absolute;
    left: 304px;
    top: 206px;
    margin: 0;
    padding: 0;
    list-style: none;
    color: var(--white);
    font-size: 13.5px;
    line-height: 22px;
  }
  .contact-list li { display: flex; align-items: center; gap: 6px; white-space: nowrap; }
  .contact-list svg { width: 12px; height: 12px; flex: none; }

  .back-website {
    position: absolute;
    top: 215px;
    left: 0;
    width: 100%;
    text-align: center;
    color: var(--white);
    font-size: 14px;
    letter-spacing: 3px;
  }
</style>
</head>
<body>
<main class="canvas">

  <section class="card card--front" aria-label="Business card front">
    <svg class="card__waves" viewBox="0 0 525 300" preserveAspectRatio="none" aria-hidden="true">
      <path d="M0,200 Q260,238 525,138 L525,150 Q260,252 0,216 Z" fill="var(--lilac)"/>
      <path d="M0,218 Q260,254 525,152 L525,300 L0,300 Z" fill="var(--royal)"/>
    </svg>

    <p class="holder-name">Rowan Ellis Hartley</p>

    <h1 class="wordmark">
      <span class="wordmark__name">Ellery Vance</span>
      <span class="wordmark__trade">FINE JEWELRY</span>
    </h1>

    <address class="store-address">2210 Linden Boulevard<br>Harbor Springs, FL 32408</address>
    <span class="divider" aria-hidden="true"></span>

    <ul class="contact-list">
      <li>
        <svg viewBox="0 0 12 12" aria-hidden="true"><circle cx="6" cy="6" r="6" fill="#fff"/><path d="M4 3.2l1 1.3-.6.8c.4.9 1.1 1.6 2 2l.8-.6 1.3 1-.6 1c-2.2-.3-4.1-2.2-4.4-4.4z" fill="var(--royal)"/></svg>
        555-318-2046
      </li>
      <li>
        <svg viewBox="0 0 12 12" aria-hidden="true"><circle cx="6" cy="6" r="6" fill="#fff"/><rect x="3" y="4" width="6" height="4" fill="none" stroke="var(--royal)" stroke-width="0.9"/><path d="M3 4l3 2.3L9 4" fill="none" stroke="var(--royal)" stroke-width="0.9"/></svg>
        rowan@elleryvancejewelry.com
      </li>
      <li>
        <svg viewBox="0 0 12 12" aria-hidden="true"><circle cx="6" cy="6" r="6" fill="#fff"/><circle cx="6" cy="6" r="3.3" fill="none" stroke="var(--royal)" stroke-width="0.8"/><ellipse cx="6" cy="6" rx="1.4" ry="3.3" fill="none" stroke="var(--royal)" stroke-width="0.8"/><path d="M2.7 6h6.6" stroke="var(--royal)" stroke-width="0.8"/></svg>
        www.elleryvancejewelry.com
      </li>
    </ul>
  </section>

  <section class="card card--back" aria-label="Business card back">
    <h2 class="wordmark">
      <span class="wordmark__name">Ellery Vance</span>
      <span class="wordmark__trade">FINE JEWELRY</span>
    </h2>
    <p class="back-website">www.elleryvancejewelry.com</p>
  </section>

</main>
</body>
</html>
```